RK Donnelly & Associates

Create a website encompassing design work already carried out for business card.
Small accounting practice, business accounting and management, superannuation, audit, taxation.

```html
<!DOCTYPE html>
<html lang="en">
<head>
<meta charset="utf-8">
<title>RK Donnelly &amp; Associates</title>
<link href="https://fonts.googleapis.com/css2?family=Open+Sans:ital,wght@0,300;0,400;0,600;1,400&display=swap" rel="stylesheet">
<style>
:root{
  --ink:#1b1b1b;
  --text:#444;
  --heading:#222;
  --accent:#4f93cf;
  --accent-soft:#6aa7dc;
  --panel:#f6f6f6;
  --white:#fff;
}
*{margin:0;padding:0;box-sizing:border-box}
html,body{width:728px;height:1200px;overflow:hidden}
body{position:relative;background:var(--white);font-family:"Open Sans",Arial,sans-serif;color:var(--text)}
.abs{position:absolute}

.site-header{left:0;top:0;width:728px;height:62px;background:var(--ink)}
.brand{left:117px;top:14px;display:flex;align-items:center;gap:7px}
.brand-mark{width:16px;height:16px;background:var(--accent-soft)}
.brand-name{color:var(--white);font-weight:600;font-size:11.5px;line-height:13px;width:110px}
.tagline{left:73px;top:49px;width:179px;height:13px;background:var(--accent-soft);color:var(--white);font-size:4.6px;line-height:13px;padding-left:6px;white-space:nowrap}
.main-nav{top:26px;left:412px;display:flex;font-size:8px;color:var(--white)}
.main-nav a{color:var(--white);text-decoration:none;padding:0 16px;border-left:1px solid #ddd;line-height:11px}
.main-nav a:first-child{border-left:none}

.hero{left:73px;top:62px;width:582px;height:256px;background:linear-gradient(100deg,#6d7f92 0%,#3a4654 30%,#aeb9c4 55%,#2d3645 75%,#c7d6e2 100%)}
.hero-arrow{top:180px;width:20px;height:20px;background:rgba(255,255,255,.45)}
.hero-arrow.prev{left:73px}.hero-arrow.next{left:635px}

.section-title{left:0;width:728px;text-align:center;color:var(--accent);font-weight:400;font-size:13.5px}
.intro{left:94px;width:540px;text-align:center;font-size:7.4px;line-height:13.6px}

.services{left:0;top:495px;width:728px;height:536px;background:var(--panel)}
.service{width:162px}
.service h3{font-weight:400;font-size:13px;color:var(--heading);height:18px}
.service .photo{width:160px;height:142px;margin-top:0}
.service p{font-size:7.2px;line-height:13.6px;margin-top:7px}
.service .more{display:flex;align-items:center;gap:4px;font-size:7.2px;color:var(--heading);margin-top:4px}
.more-dot{width:8px;height:8px;border-radius:50%;background:var(--accent)}

.avatar{left:84px;top:1068px;width:84px;height:84px;border-radius:50%;background:radial-gradient(circle at 50% 40%,#d9b59a 0 30%,#2b3a55 60%,#eef1f4 61%)}
.quote{left:211px;top:1084px;width:350px;font-style:italic;font-size:8.4px;line-height:13.6px;color:#555}
.qmark{font-size:18px;color:var(--accent-soft);font-style:normal;font-family:Georgia,serif}

.site-footer{left:0;top:1171px;width:728px;height:29px;background:var(--ink);color:var(--white);font-size:7.6px}
.site-footer .item{position:absolute;top:9px;display:flex;align-items:center;gap:6px}
.social{position:absolute;left:510px;top:10px;display:flex;gap:4px}
.social span{width:9px;height:9px;border-radius:50%;background:var(--white)}
</style>
</head>
<body>

<header class="site-header abs">
  <div class="brand abs"><span class="brand-mark"></span><span class="brand-name">RK Donnelly &amp; Associates</span></div>
  <nav class="main-nav abs"><a href="#">Home</a><a href="#">About us</a><a href="#">Services</a><a href="#">Conatct us</a></nav>
</header>
<div class="tagline abs">Accountant · Business Solutions · Management · Superannuation · Audit</div>

<div class="hero abs" role="img" aria-label="Smiling businesswoman holding folders in front of colleagues in an office"></div>
<div class="hero-arrow prev abs"><svg width="20" height="20"><path d="M12 5 L7 10 L12 15" stroke="#fff" fill="none" stroke-width="1.2"/></svg></div>
<div class="hero-arrow next abs"><svg width="20" height="20"><path d="M8 5 L13 10 L8 15" stroke="#fff" fill="none" stroke-width="1.2"/></svg></div>

<h1 class="section-title abs" style="top:333px">Welcome to RK Donnelly &amp; Associates</h1>
<p class="intro abs" style="top:362px">Proin gravida nibh vel velit auctor aliquet. Aenean sollicitudin, lorem quis bibendum auctor, nisi elit consequat ipsum, nec sagittis sem nibh id elit. Duis sed odio sit amet nibh vulputate cursus a sit amet mauris. Morbi accumsan ipsum velit. Nam nec tellus a odio tincidunt auctor a ornare odio. Sed non mauris vitae erat consequat auctor eu in elit. Class aptent taciti sociosqu ad litora torquent per conubia nostra.</p>

<h2 class="section-title abs" style="top:430px">Services We Provide</h2>
<p class="intro abs" style="top:457px;left:84px;width:560px">Lorem psumroin gravida nibh vel velit auctor aliquet. Aenean sollicitudin, lorem quis bibendum auctor, nisi elit consequat ipsum, nec sagittis sem nibh id elit. sed odio sit amet nibh vulputate cursus a sit amet mauris. Morbi accumsan ipsum velit. Nam nec tellus a odio tincidunt auctor a ornare odio.</p>

<section class="services abs"></section>

<article class="service abs" style="left:95px;top:524px">
  <h3>Accounting Practice</h3>
  <div class="photo" role="img" aria-label="Hands working on a tablet over financial charts" style="background:linear-gradient(135deg,#2a3447,#dfe6ee 55%,#9fb3c9)"></div>
  <p>Lorem Ipsum roin gravida nibh vel velit auctor aliquetes aenean sollicitudin, lorem quiseed endum auctor, nisi elit consequat ipsum.</p>
  <div class="more">more <span class="more-dot"></span></div>
</article>
<article class="service abs" style="left:294px;top:524px">
  <h3>Business Solutions</h3>
  <div class="photo" role="img" aria-label="Cupped hands holding soil with a young plant" style="background:radial-gradient(circle at 50% 55%,#4a3322 0 20%,#b98a6b 45%,#d9d4d0 80%)"></div>
  <p>Lorem Ipsum roin gravida nibh vel velit auctor aliquetes aenean sollicitudin, lorem quiseed endum auctor, nisi elit consequat ipsum.</p>
  <div class="more">more <span class="more-dot"></span></div>
</article>
<article class="service abs" style="left:495px;top:524px">
  <h3>Superannuation</h3>
  <div class="photo" role="img" aria-label="Coins beside a calculator and a pen" style="background:linear-gradient(120deg,#c9ccd0,#8f969f 50%,#4b5561)"></div>
  <p>Lorem Ipsum roin gravida nibh vel velit auctor aliquetes aenean sollicitudin, lorem quiseed endum auctor, nisi elit consequat ipsum.</p>
  <div class="more">more <span class="more-dot"></span></div>
</article>
<article class="service abs" style="left:186px;top:778px">
  <h3>Audit</h3>
  <div class="photo" role="img" aria-label="Hands holding a tablet showing charts" style="background:linear-gradient(140deg,#e8eef4,#8fb0cc 50%,#1e2430 70%,#dfe7ee)"></div>
  <p>Lorem Ipsum roin gravida nibh vel velit auctor aliquetes aenean sollicitudin, lorem quiseed endum auctor, nisi elit consequat ipsum.</p>
  <div class="more">more <span class="more-dot"></span></div>
</article>
<article class="service abs" style="left:387px;top:778px">
  <h3>Taxation</h3>
  <div class="photo" role="img" aria-label="Hand typing on a calculator with a pencil" style="background:linear-gradient(160deg,#f1e6df,#d8a98f 35%,#2a2d33 60%,#e5e8ec)"></div>
  <p>Lorem Ipsum roin gravida nibh vel velit auctor aliquetes aenean sollicitudin, lorem quiseed endum auctor, nisi elit consequat ipsum.</p>
  <div class="more">more <span class="more-dot"></span></div>
</article>

<h2 class="section-title abs" style="top:1047px;left:-78px">Satisfied Customers</h2>
<div class="avatar abs" role="img" aria-label="Portrait of a smiling client in a suit"></div>
<span class="qmark abs" style="left:196px;top:1074px">“</span>
<blockquote class="quote abs">Lorem Ipsum. Proin gravida nibh vel velit auctor aliquet. Aenean sollicitudin lorem quis bibendum auctor, nisi elit consequat ipsum, nec sagittis sem nibh id elit. Duis sed odio sit amet nibh vulputate cursus a sit amet mauris.</blockquote>
<span class="qmark abs" style="left:476px;top:1116px">”</span>

<footer class="site-footer abs">
  <div class="item" style="left:162px">© 2013 rkdonnelly.com</div>
  <div class="item" style="left:268px"><svg width="8" height="7"><rect x=".5" y=".5" width="7" height="6" fill="none" stroke="#fff"/><path d="M.5 .5 L4 4 L7.5 .5" fill="none" stroke="#fff"/></svg>hello@rkdonnelly-mail.com</div>
  <div class="item" style="left:396px"><svg width="8" height="8"><path d="M1 2 Q1 7 6 7 L7 5.5 L5 4.5 L4 5.5 Q2.5 4.5 2.5 4 L3.5 3 L2.5 1 Z" fill="#fff"/></svg>+61 3 5550 2417</div>
  <div class="social"><span></span><span></span><span></span><span></span><span></span></div>
</footer>

</body>
</html>
```